Business card por a urban DJ, up scale audience target

Need a sober design, modern, conservative colors but i can consider some options, y play rnb, hip hop, EDM and top40.

Business card for contact and personal info, double sided, use logo attrached please; im 42 so i need a card acording to my age an target audience.

Target Market(s)

Adult people, up scale audience

Industry/Entity Type

Music Download

Contact Information for Business Card

Cel (318) 4207265518 www.lumadrift.com

Requirements
Must have
• open mind
Nice to have
• open mind
Should not have
• DJ

```html
<!DOCTYPE html>
<html lang="en">
<head>
<meta charset="utf-8">
<title>Luma Business Card</title>
<link href="https://fonts.googleapis.com/css2?family=Arimo:wght@400;700&display=swap" rel="stylesheet">
<style>
  :root{
    --stage:#e6e4e1;
    --paper:#ffffff;
    --ink-dark:#2e2e2e;
    --ink-black:#1c1c1c;
    --band-grey:#8a8a8a;
    --logo-grey:#444444;
    --text-light:#f2f2f2;
    --text-muted:#cfcfcf;
  }
  *{margin:0;padding:0;box-sizing:border-box}
  html,body{width:1200px;height:892px;overflow:hidden;background:var(--stage);font-family:"Arimo",Arial,sans-serif}
  .canvas{width:1200px;height:892px;display:flex;flex-direction:column;align-items:center;justify-content:center;gap:30px}
  .card{position:relative;width:700px;height:400px;overflow:hidden;box-shadow:0 6px 18px rgba(0,0,0,.18)}
  .card-front{background:var(--paper)}
  .card-back{background:var(--ink-black)}
  .wave{position:absolute;inset:0;width:100%;height:100%}
  .brand{position:absolute;font-weight:700;letter-spacing:2px;line-height:1}
  .brand-front{left:50px;top:120px;font-size:88px;color:var(--logo-grey)}
  .brand-back{left:50%;top:50%;transform:translate(-50%,-50%);font-size:130px;color:var(--paper)}
  .contact{position:absolute;right:34px;top:34px;width:290px;color:var(--text-light);text-align:right}
  .contact-name{font-size:26px;font-weight:700}
  .contact-role{font-size:15px;color:var(--text-muted);margin-top:4px}
  .contact-icons{display:flex;justify-content:flex-end;gap:8px;margin:14px 0 18px}
  .contact-icons svg{width:20px;height:20px}
  .contact-line{font-size:16px;line-height:1.6}
  .contact-address{font-size:15px;margin-top:22px}
</style>
</head>
<body>
<main class="canvas">
  <section class="card card-front">
    <svg class="wave" viewBox="0 0 700 400" preserveAspectRatio="none" aria-hidden="true">
      <path d="M440 0 C370 50 400 220 320 290 C250 350 150 358 0 358 L0 400 L700 400 L700 0 Z" fill="var(--band-grey)"/>
      <path d="M470 0 C395 55 425 235 340 305 C265 362 160 372 0 374 L0 400 L700 400 L700 0 Z" fill="var(--ink-dark)"/>
    </svg>
    <div class="brand brand-front">LUMA</div>
    <div class="contact">
      <div class="contact-name">Owen Calder</div>
      <div class="contact-role">Director</div>
      <div class="contact-icons" aria-hidden="true">
        <svg viewBox="0 0 20 20"><rect width="20" height="20" fill="var(--text-light)"/><path d="M6 4l3 3-1.5 1.5c1 2 2 3 4 4L13 11l3 3-2 2C9 15 5 11 4 6z" fill="var(--ink-dark)"/></svg>
        <svg viewBox="0 0 20 20"><rect width="20" height="20" fill="var(--text-light)"/><rect x="4" y="6" width="12" height="8" fill="none" stroke="var(--ink-dark)" stroke-width="1.5"/><path d="M4 6l6 5 6-5" fill="none" stroke="var(--ink-dark)" stroke-width="1.5"/></svg>
        <svg viewBox="0 0 20 20"><rect width="20" height="20" fill="var(--text-light)"/><circle cx="10" cy="10" r="6" fill="none" stroke="var(--ink-dark)" stroke-width="1.5"/><path d="M4 10h12M10 4c-3 3-3 9 0 12M10 4c3 3 3 9 0 12" fill="none" stroke="var(--ink-dark)" stroke-width="1.2"/></svg>
        <svg viewBox="0 0 20 20"><rect width="20" height="20" fill="var(--text-light)"/><path d="M10 17s-5-5-5-9a5 5 0 0110 0c0 4-5 9-5 9z" fill="var(--ink-dark)"/><circle cx="10" cy="8" r="2" fill="var(--text-light)"/></svg>
      </div>
      <div class="contact-line">(318) 4207265518</div>
      <div class="contact-line">info@lumadrift.com</div>
      <div class="contact-line">www.lumadrift.com</div>
      <div class="contact-address">PO Box 4418 Maple Rise SA 5072</div>
    </div>
  </section>
  <section class="card card-back">
    <div class="brand brand-back">LUMA</div>
  </section>
</main>
</body>
</html>
```